BrimFalcon Business Cards

We have a defined brand. Please visit our website to get a feel for the product and the color pallets. www.brimfalcon-example.com

We need an updated, world class business card design. (See the attached existing card design). Please utilize BOTH sides of the card as shown and be creative with the layout. I do want the horse head icon to be positioned as it is with the existing card.

The remainder of the layout can be customized and I also want it vertically oriented.

Attached are the logo files and please use the colors as follows:
Green - #A5CE39
Tan - #CDBD99
Black

Feel free to play with the colors.

```html
<!DOCTYPE html>
<html lang="en">
<head>
<meta charset="utf-8">
<title>BrimFalcon Labs Business Card</title>
<link href="https://fonts.googleapis.com/css2?family=Montserrat:wght@400;600;800&display=swap" rel="stylesheet">
<style>
  :root {
    --stage: #3a3a3c;
    --card-dark: #232324;
    --ink: #0b0b0b;
    --white: #f4f4f4;
    --lime: #a5ce39;
    --lime-bright: #c4dc2e;
    --forest: #0e7a22;
    --green-top: #a8c934;
    --green-bottom: #3b8a40;
  }
  * { box-sizing: border-box; margin: 0; padding: 0; }
  html, body { width: 1200px; height: 1108px; overflow: hidden; }
  body {
    background: var(--stage);
    font-family: "Montserrat", sans-serif;
    position: relative;
  }
  .card {
    position: absolute;
    top: 234px;
    width: 400px;
    height: 640px;
    border-radius: 26px;
    overflow: hidden;
    box-shadow: 0 14px 30px rgba(0,0,0,0.45);
  }
  /* Front: contact side */
  .card-front { left: 170px; background: var(--card-dark); color: var(--white); }
  .brand-lockup {
    position: absolute; top: 80px; left: 36px; right: 36px;
    display: flex; flex-direction: column; align-items: center;
  }
  .brand-row { display: flex; align-items: center; gap: 10px; }
  .brand-dot { width: 28px; height: 28px; border-radius: 50%; background: var(--white); flex: none; }
  .brand-name { font-weight: 800; font-size: 28px; letter-spacing: 0.3px; color: var(--white); white-space: nowrap; }
  .brand-tagline { margin-top: 8px; font-size: 13px; font-weight: 600; letter-spacing: 3px; color: var(--white); }
  .name-band {
    position: absolute; top: 220px; left: 0; right: 0; height: 106px;
    background: linear-gradient(90deg, var(--forest) 0%, var(--lime-bright) 50%, var(--forest) 100%);
    display: flex; flex-direction: column; align-items: center; justify-content: center;
    color: var(--ink);
  }
  .person-name { font-weight: 800; font-size: 30px; letter-spacing: 1px; text-transform: uppercase; }
  .person-title { font-weight: 600; font-size: 15px; margin-top: 2px; }
  .contact {
    position: absolute; top: 400px; left: 30px; right: 30px;
    text-align: center; font-size: 18px; line-height: 25px; font-weight: 400;
  }
  .contact .gap { height: 14px; }
  /* Back: brand side */
  .card-back {
    left: 630px;
    background: linear-gradient(180deg, var(--green-top) 0%, var(--green-bottom) 100%);
  }
  .back-brand { position: absolute; top: 84px; left: 32px; right: 32px; text-align: center; }
  .back-name { font-weight: 800; font-size: 32px; color: var(--ink); letter-spacing: 0.3px; white-space: nowrap; }
  .back-slogan { margin-top: 10px; font-weight: 600; font-size: 18px; letter-spacing: 2.5px; color: var(--white); }
  .emblem-art {
    position: absolute; left: 0; bottom: 0; width: 360px; height: 400px;
    border-radius: 0 60% 0 26px;
    background: linear-gradient(160deg, #111 0%, #1a3a1c 70%, #2f7a35 100%);
  }
</style>
</head>
<body>
  <section class="card card-front">
    <div class="brand-lockup">
      <div class="brand-row">
        <span class="brand-dot"></span>
        <span class="brand-name">BrimFalcon Labs</span>
      </div>
      <div class="brand-tagline">Performance Driven EVs</div>
    </div>
    <div class="name-band">
      <div class="person-name">Marcus Delane</div>
      <div class="person-title">President &amp; CEO</div>
    </div>
    <div class="contact">
      <p>BrimFalcon Labs</p>
      <p>Harrow Plains, Prairieland</p>
      <p>Canada</p>
      <div class="gap"></div>
      <p>P. 306.555.0148</p>
      <p>marcus@brimfalcon-example.com</p>
      <p>brimfalconlabs-example.com</p>
    </div>
  </section>

  <section class="card card-back">
    <div class="back-brand">
      <div class="back-name">BrimFalcon Labs</div>
      <div class="back-slogan">MOBILOITY REIMAGINED</div>
    </div>
    <div class="emblem-art" role="img" aria-label="Large brand emblem illustration in black and green"></div>
  </section>
</body>
</html>
```